Website for new dental office

I am Dr. Colin Ashford and am building a new dental practice. I specialize in general dentistry. I am young and have a higher end dental practice incorporating very new technologies and would like my website to reflect that. As many dental patients are older, the website must be very easy to navigate. I would like patients to be able to request appointments, and will eventually add on patient information forms (the health history, etc, that you normally fill out in the practice) from my practice management software, so leave an area for that.

Industry/Entity Type

Building

```html
<!DOCTYPE html>
<html lang="en">
<head>
<meta charset="utf-8">
<title>Colin Ashford, DDS — Our Portfolio</title>
<link href="https://fonts.googleapis.com/css2?family=Open+Sans:wght@300;400;600;700&display=swap" rel="stylesheet">
<style>
:root{
  --blue:#1f7fd6;
  --blue-deep:#1d5fa3;
  --nav-top:#3a90e0;
  --nav-bottom:#1b6cc2;
  --nav-active:#15519a;
  --ink:#333;
  --muted:#666;
  --orange-top:#ffa640;
  --orange-bottom:#f58414;
  --panel:#f7f7f7;
}
*{margin:0;padding:0;box-sizing:border-box}
html,body{width:1067px;height:1200px;overflow:hidden;background:#fff}
body{font-family:"Open Sans",Arial,sans-serif;color:var(--ink);position:relative}
.site-header{position:absolute;left:0;top:0;width:1067px;height:103px;background:linear-gradient(#e0eefc,#fff)}
.brand{position:absolute;left:96px;top:38px;font-size:28px;font-weight:600;color:var(--blue);letter-spacing:.5px}
.phone{position:absolute;left:738px;top:33px;display:flex;align-items:center;gap:10px;font-size:23px;color:#444}
.main-nav{position:absolute;left:0;top:103px;width:1067px;height:39px;background:linear-gradient(var(--nav-top),var(--nav-bottom))}
.main-nav a{position:absolute;top:0;height:39px;line-height:39px;color:#fff;text-decoration:none;font-size:13.5px;text-transform:uppercase}
.main-nav a.home{font-weight:700}
.main-nav a.active{background:var(--nav-active);width:126px;text-align:center}
.nav-sep{position:absolute;top:10px;width:1px;height:20px;background:rgba(255,255,255,.3)}
.hero{position:absolute;left:0;top:142px;width:1067px;height:226px;background:linear-gradient(90deg,#c9d8e4 0%,#eef3f8 30%,#fff 60%);border-bottom:1px solid #d6e4ef;overflow:hidden}
.hero h1{position:absolute;left:95px;top:60px;font-size:53px;font-weight:300;color:var(--blue-deep);line-height:1}
.hero h1 strong{font-weight:700}
.hero p{position:absolute;left:96px;top:124px;width:430px;font-size:18px;line-height:24px;color:#222}
.hero-art{position:absolute;left:570px;top:0;width:400px;height:226px;background:linear-gradient(90deg,rgba(236,239,242,0) 0%,#eceff2 30%,#f3f4f6 70%,rgba(243,244,246,0) 100%)}
.section-title{position:absolute;left:94px;top:403px;font-size:21px;font-weight:400;color:var(--blue);line-height:1.2}
.section-rule{position:absolute;left:219px;top:416px;width:732px;height:4px;border-top:1px dotted #bbb;border-bottom:1px dotted #bbb}
.section-rule::before{content:"";position:absolute;left:0;top:0;width:189px;height:3px;background:var(--blue)}
.case{position:absolute;width:396px}
.case .photo{height:124px;width:386px}
.case h2{margin-top:16px;font-size:18px;font-weight:600;color:var(--blue)}
.case p{margin-top:10px;font-size:11.5px;line-height:15.3px;color:var(--muted)}
.cta{position:absolute;left:95px;top:1024px;width:854px;height:92px;background:var(--panel);border:1px solid #e3e3e3;border-radius:6px}
.cta p{position:absolute;left:14px;top:30px;font-size:23px;color:#555;white-space:nowrap}
.cta a{position:absolute;left:615px;top:21px;width:225px;height:51px;border-radius:3px;background:linear-gradient(var(--orange-top),var(--orange-bottom));color:#fff;text-decoration:none;font-size:17px;font-weight:600;display:flex;align-items:center;justify-content:center;gap:10px}
.site-footer{position:absolute;left:0;top:1147px;width:1033px;text-align:center;font-size:12px;color:#222}
</style>
</head>
<body>
<header class="site-header">
  <div class="brand">COLIN ASHFORD, DDS</div>
  <div class="phone">
    <svg width="36" height="36" viewBox="0 0 36 36" aria-hidden="true">
      <circle cx="22" cy="14" r="11" fill="none" stroke="#1f7fd6" stroke-width="2"/>
      <text x="22" y="18.5" font-size="11" font-weight="700" fill="#1f7fd6" text-anchor="middle" font-family="Open Sans,sans-serif">24</text>
      <path d="M6 8c-3 3-2 10 5 18s14 9 17 6l-4-5-4 2c-3-1-8-7-9-10l2-4z" fill="#333"/>
    </svg>
    <span>123 555 0148</span>
  </div>
</header>

<nav class="main-nav">
  <a class="home" href="#" style="left:96px">Home</a>
  <span class="nav-sep" style="left:163px"></span>
  <a href="#" style="left:193px">Services</a>
  <span class="nav-sep" style="left:283px"></span>
  <a href="#" style="left:310px">Resources</a>
  <a class="active" href="#" style="left:402px">Portfolio</a>
  <a href="#" style="left:564px">Team</a>
  <span class="nav-sep" style="left:619px"></span>
  <a href="#" style="left:643px">Contact</a>
</nav>

<section class="hero">
  <h1>Our <strong>Portfolio</strong></h1>
  <p>Lorem Ipsum is simply dummy text of the printing and typesetting industry. Lorem Ipsum has been</p>
  <div class="hero-art" role="img" aria-label="Illustration of a large white tooth beside a figure holding a first-aid case"></div>
</section>

<h2 class="section-title">Our Portolio</h2>
<div class="section-rule"></div>

<article class="case" style="left:98px;top:460px">
  <div class="photo" role="img" aria-label="Photo of a smiling woman biting a green apple" style="background:linear-gradient(90deg,#4c6a3c,#7f8d62 45%,#c9a996 75%,#3a2a22)"></div>
  <h2>Cosmetics</h2>
  <p>Lorem Ipsum is simply dummy text of the printing and typesetting industry. Lorem Ipsum has been the industry's standard dummy text ever since the 1500s, Lorem Ipsum is simply dummy text of the printing and typesetting industry. Lorem Ipsum has been the industry's standard dummy text ever since the 1500s,</p>
</article>

<article class="case" style="left:567px;top:460px">
  <div class="photo" role="img" aria-label="Photo of a clear dental implant model" style="background:linear-gradient(90deg,#6a4a2a,#b07a3a 35%,#c9c2b8 60%,#e6e8ea)"></div>
  <h2>Restorative</h2>
  <p>Lorem Ipsum is simply dummy text of the printing and typesetting industry. Lorem Ipsum has been the industry's standard dummy text ever since the 1500s, Lorem Ipsum is simply dummy text of the printing and typesetting industry. Lorem Ipsum has been the industry's standard dummy text ever since the 1500s,</p>
</article>

<article class="case" style="left:96px;top:735px">
  <div class="photo" role="img" aria-label="Close-up photo of a bright smile" style="background:linear-gradient(90deg,#e8c6bc,#f3e4de 40%,#e4eede 70%,#f4f7f2)"></div>
  <h2>Cosmetics</h2>
  <p>Lorem Ipsum is simply dummy text of the printing and typesetting industry. Lorem Ipsum has been the industry's standard dummy text ever since the 1500s, Lorem Ipsum is simply dummy text of the printing and typesetting industry. Lorem Ipsum has been the industry's standard dummy text ever since the 1500s,</p>
</article>

<article class="case" style="left:565px;top:735px">
  <div class="photo" role="img" aria-label="Two panoramic dental X-ray images" style="background:linear-gradient(90deg,#2a2a2a,#8a8a8a 25%,#3a3a3a 49.5%,#fff 49.5%,#fff 50.5%,#3a3a3a 50.5%,#8a8a8a 75%,#2a2a2a)"></div>
  <h2>Restorative</h2>
  <p>Lorem Ipsum is simply dummy text of the printing and typesetting industry. Lorem Ipsum has been the industry's standard dummy text ever since the 1500s, Lorem Ipsum is simply dummy text of the printing and typesetting industry. Lorem Ipsum has been the industry's standard dummy text ever since the 1500s,</p>
</article>

<aside class="cta">
  <p>Want to Get Treated? Schedule Your Appointment Now!</p>
  <a href="#">Request Appointment
    <svg width="22" height="22" viewBox="0 0 22 22" aria-hidden="true" fill="none" stroke="#333" stroke-width="1.5">
      <rect x="1" y="3" width="20" height="18" rx="1"/>
      <line x1="1" y1="7" x2="21" y2="7"/>
      <line x1="6" y1="1" x2="6" y2="5"/><line x1="16" y1="1" x2="16" y2="5"/>
      <g fill="#333" stroke="none"><rect x="4" y="10" width="3" height="2"/><rect x="9.5" y="10" width="3" height="2"/><rect x="15" y="10" width="3" height="2"/><rect x="4" y="15" width="3" height="2"/><rect x="9.5" y="15" width="3" height="2"/><rect x="15" y="15" width="3" height="2"/></g>
    </svg>
  </a>
</aside>

<footer class="site-footer">© Copyrights 2014 All rights Reserved</footer>
</body>
</html>
```